Online Psychiatry business - Business Card

I need a business card design. The target audience is busy professionals of any field (this therapy appeals best to 24-35 year olds). It involves psychiatry by tele-medicine (or video-conference). Nothing on it should be a giveaway that it's about mental health. Professional design with silver or gold as the primary colors appeals to me. The card must be as simple and as uncluttered as possible. Some color and flowing design on the edge of the card appeals to me.
CalmHarborDirect.net should probably appear in the center of the card and stand out, i.e. bold lettering, and easy to read, no cursive, but Ariel Black. Some where below this, should appear "Too Busy to Take Care of Yourself? Think again." Since this isn't office based, I don't think an office address is necessary and limits clutter.
Information that does need to appear is my name: Gerald Mossvane, MD
General phone number: 555-417-8062. I'm hoping to get an 24-hour answering service soon so leave a little room for this. In addition I want to include two email addresses:
CalmHarborDirect@mailbox-example.net and CalmHarbor247@mailbox-example.net
Updates

I like the designs. I would like someone to put the website in bold in the center

 as most have been doing with a smaller font reminder nearby saying "No time" etc.
but I'd like to put my name down in the corner with the rest of the contact material.
Black print against a white or grey background appeals to me, with darker silver artwork near the sides (simple abstract, like wavy lines or something you can one up with that works. 
thanks

I ve tried to provide as much feedback as possible given my time limits, so if you have extra questions, please feel free to email. I tried to attach a file of a business card I really like but make be difficult to actually manufacture. I'm going to send you a link to the photo. The card has a pull tab. There is not much information on the outside. In fact, if you were to design the outside, I would just print : Too Busy to Take Care of Yourself? Think Again.

When you pull the tab the remaining information is on the bottom half of the card. Please don't use the color pink!!!!
http://www.cardgallery-example.org/2009/05/100-clever-print-ideas/
It is the 39th photo on the list, about 2/3ds of the way down the page. It is titled: Faltenkiste

#7 and #16 have an appeal to me, except for the dot patterns
Hope this helps

I'm running out of time and energy. I 've been trying to give do down the list and give  individual feedback but I won't be able to do that anymore.

So if you have any specific questions, write me, and again thank you for all your effort!!

I know i received your files, including your zip files, Pindrel,

but Milo, did you send me the files including ZIP on project 6143907?
thanks

Target Market(s)

Working professionals and executive, attorneys, etc.

Industry/Entity Type

Business

Logo Text

Don't Have Time to Take Care of Yourself? Think Again.

Logo styles of interest
Pictorial/Combination Logo
Wordmark Logo
Font styles to use
Other font styles liked:
• Ariel Black appeals to me the most

Requirements
Must have
• Want to emphasize that the website must be obvious, easily found (The CalmHarborDirect.net)
For that reason i'd like the card to be white, and minimal decoration on one or both sides just to add some style and color
Nice to have
• A Very uncluttered, elegant design, and something that makes it stick in your head-doesn't everyone want the last?
Should not have
• Nothing on the card that give it away that this is about psychiatry, such as brain or other symbol, but also nothing that gives it away as a medical business, such as a stethoscope or red cross or anything.

```html
<!DOCTYPE html>
<html lang="en">
<head>
<meta charset="utf-8">
<title>CalmHarborDirect.net – Business Card</title>
<link href="https://fonts.googleapis.com/css2?family=Arimo:wght@400;700&display=swap" rel="stylesheet">
<style>
  :root {
    --backdrop: #4a3d33;
    --card-white: #ffffff;
    --card-grey: #e6e6e6;
    --ink-dark: #333333;
    --ink-black: #111111;
    --accent-orange: #e59a2f;
    --gold-light: #fbf1a6;
    --gold-mid: #e6c86a;
    --gold-deep: #b8893a;
    --gold-edge: #9c7330;
  }
  * { box-sizing: border-box; margin: 0; padding: 0; }
  html, body { width: 1200px; height: 418px; overflow: hidden; }
  body {
    background: var(--backdrop);
    font-family: "Arimo", Arial, sans-serif;
    position: relative;
  }
  .card {
    position: absolute;
    top: 90px;
    width: 464px;
    height: 266px;
    overflow: hidden;
    box-shadow: 0 4px 12px rgba(0,0,0,0.45);
  }

  /* Front */
  .card--front {
    left: 124px;
    background: radial-gradient(ellipse at 55% 35%, var(--card-white) 40%, var(--card-grey) 100%);
  }
  .site-name {
    position: absolute;
    left: 0; right: 0;
    text-align: center;
    font-weight: 700;
  }
  .card--front .site-name {
    top: 168px - 0px;
    top: 168px;
    top: 166px;
  }
  .card--front .site-name { top: 76px; font-size: 27px; color: var(--ink-dark); }
  .tagline--front {
    position: absolute;
    top: 122px; left: 0; right: 0;
    text-align: center;
    font-size: 13px;
    color: var(--accent-orange);
  }
  .contact-band {
    position: absolute;
    left: 0; right: 0;
    top: 222px; height: 34px;
    background: linear-gradient(90deg, var(--gold-light) 0%, var(--gold-mid) 45%, var(--gold-deep) 100%);
    border-top: 1px solid var(--gold-edge);
    border-bottom: 1px solid var(--gold-edge);
  }
  .phone {
    position: absolute;
    left: 26px; top: 10px;
    font-size: 12px;
    color: var(--accent-orange);
  }
  .phone strong { color: var(--ink-black); font-size: 13px; }
  .emails {
    position: absolute;
    right: 22px; top: 3px;
    text-align: right;
    font-size: 10.5px;
    line-height: 14px;
    color: var(--ink-black);
  }

  /* Back */
  .card--back {
    left: 628px;
    background: linear-gradient(180deg, var(--gold-light) 0%, var(--gold-mid) 55%, var(--gold-deep) 100%);
  }
  .card--back .site-name {
    top: 94px;
    font-size: 28px;
    color: var(--card-white);
    text-shadow: 1px 2px 3px rgba(80,55,10,0.6);
  }
  .tagline--back {
    position: absolute;
    top: 139px; left: 0; right: 0;
    text-align: center;
    font-size: 11px;
    font-weight: 700;
    letter-spacing: 0.3px;
    color: var(--ink-black);
  }
  .service-band {
    position: absolute;
    left: 0; right: 0;
    top: 220px; height: 34px;
    background: linear-gradient(90deg, var(--gold-deep) 0%, var(--gold-mid) 40%, var(--gold-light) 100%);
    border-top: 1px solid var(--gold-edge);
    border-bottom: 1px solid var(--gold-edge);
    display: flex;
    align-items: center;
    justify-content: center;
    font-size: 13px;
    font-weight: 700;
    color: var(--card-white);
    text-shadow: 1px 1px 2px rgba(80,55,10,0.7);
  }
</style>
</head>
<body>
  <section class="card card--front">
    <h1 class="site-name">CalmHarborDirect.net</h1>
    <p class="tagline--front">"You're a amazing person. We should talk again."</p>
    <div class="contact-band">
      <p class="phone">General Phone: <strong>555-417-8062</strong></p>
      <p class="emails">CalmHarborDirect@mailbox-example.net<br>CalmHarbor247@mailbox-example.net</p>
    </div>
  </section>

  <section class="card card--back">
    <h2 class="site-name">CalmHarborDirect.net</h2>
    <p class="tagline--back">“NOT ENOUGH TIME TO CARE FOR YOURSELF”</p>
    <div class="service-band">24-HOUR ANSWERING SERVICE</div>
  </section>
</body>
</html>
```